80s style fun billboard for auto repair shop

A new design for our automotive shops’s advertisement billboard with an 80s-90s theme! Neon colors like photo example. Something eye catching but easy to read. Logos attached should be altered to match theme of advertisement. 1980s or 90s colors and theme. Details need to include an arrow and “1.2 miles ahead”, phone number “817-390-7148”, address “2085 W Malbury St”, and “best auto repair shop in town!” . Dimensions are 12'3"x 24'6"

Target Market(s)

Drive by attention

Industry/Entity Type

Automotive

Colors

Designer to choose colors to be used in the design.

Requirements
Must have
• My logo, address, phone number, tag line and badass 90s theme look!
Nice to have
• 80s color scheme, neon colors, use example photo for color ideas

```html
<!DOCTYPE html>
<html lang="en">
<head>
<meta charset="utf-8">
<title>Billboard – Auto &amp; Diesel Repair</title>
<link href="https://fonts.googleapis.com/css2?family=Poppins:ital,wght@0,800;1,700;1,800&display=swap" rel="stylesheet">
<style>
  :root {
    --page-bg: #e9edf2;
    --royal-blue: #2a5fb8;
    --ink-navy: #1b2442;
    --white: #ffffff;
    --teal-deep: #2f5a55;
    --teal-mid: #6f9c8c;
    --sage: #a9bf98;
    --amber: #d3a24a;
    --neon-pink: #ff3fb4;
    --neon-cyan: #3ff0ff;
    --band-dark: rgba(30, 34, 30, 0.62);
    --badge-blue: #2a86d6;
  }
  html, body {
    margin: 0;
    width: 1200px;
    height: 1200px;
    overflow: hidden;
    background: var(--page-bg);
  }
  .billboard {
    position: absolute;
    left: 20px;
    top: 315px;
    width: 1160px;
    height: 570px;
    overflow: hidden;
    font-family: "Poppins", sans-serif;
  }
  .billboard__artwork {
    position: absolute;
    inset: 0;
    background:
      radial-gradient(ellipse at 22% 62%, rgba(47, 90, 85, 0.9) 0%, rgba(47, 90, 85, 0) 55%),
      radial-gradient(ellipse at 85% 85%, rgba(211, 162, 74, 0.8) 0%, rgba(211, 162, 74, 0) 45%),
      radial-gradient(ellipse at 95% 10%, rgba(255, 63, 180, 0.35) 0%, rgba(255, 63, 180, 0) 40%),
      linear-gradient(160deg, var(--sage) 0%, var(--teal-mid) 40%, var(--teal-deep) 70%, var(--amber) 100%);
  }
  .neon-frame {
    position: absolute;
    inset: 8px;
    border: 3px solid var(--neon-pink);
    box-shadow: 0 0 12px var(--neon-pink), inset 0 0 12px var(--neon-pink);
    pointer-events: none;
  }
  .neon-rule {
    position: absolute;
    left: 0;
    width: 826px;
    height: 3px;
    background: var(--neon-cyan);
    box-shadow: 0 0 10px var(--neon-cyan);
  }
  .neon-rule--top { top: 309px; }
  .neon-rule--bottom { top: 404px; }
  .headline {
    position: absolute;
    left: 244px;
    top: 26px;
    margin: 0;
    font-weight: 800;
    font-style: italic;
    font-size: 74px;
    line-height: 90px;
    letter-spacing: -1px;
    color: var(--royal-blue);
    -webkit-text-stroke: 3px var(--white);
    paint-order: stroke fill;
    text-shadow: 5px 5px 0 var(--ink-navy);
    white-space: nowrap;
  }
  .phone-band {
    position: absolute;
    left: 0;
    top: 312px;
    width: 826px;
    height: 92px;
    background: var(--band-dark);
  }
  .phone {
    position: absolute;
    left: 244px;
    top: 314px;
    margin: 0;
    font-weight: 800;
    font-style: italic;
    font-size: 72px;
    line-height: 88px;
    color: var(--white);
    letter-spacing: 1px;
  }
  .shop-name {
    position: absolute;
    left: 28px;
    top: 122px;
    width: 200px;
    display: flex;
    align-items: center;
    gap: 10px;
    font-weight: 800;
    font-size: 24px;
    line-height: 28px;
    color: var(--white);
  }
  .shop-name__mark {
    flex: none;
    width: 22px;
    height: 22px;
    background: var(--royal-blue);
  }
  .cert-badge {
    position: absolute;
    left: 56px;
    top: 430px;
  }
  .tagline {
    position: absolute;
    left: 190px;
    top: 424px;
    margin: 0;
    font-weight: 800;
    font-style: italic;
    font-size: 26px;
    line-height: 34px;
    color: var(--white);
    text-shadow: 0 0 8px var(--neon-pink), 2px 2px 0 var(--ink-navy);
  }
  .directions {
    position: absolute;
    left: 620px;
    top: 388px;
  }
  .directions__distance {
    position: absolute;
    left: 652px;
    top: 446px;
    margin: 0;
    font-weight: 800;
    font-style: italic;
    font-size: 42px;
    line-height: 60px;
    color: var(--white);
    white-space: nowrap;
  }
  .directions__address {
    position: absolute;
    left: 660px;
    top: 516px;
    margin: 0;
    font-weight: 700;
    font-style: italic;
    font-size: 32px;
    line-height: 42px;
    color: var(--white);
    white-space: nowrap;
  }
</style>
</head>
<body>
  <section class="billboard">
    <div class="billboard__artwork" role="img" aria-label="Retro illustration of a vintage car dashboard and steering wheel in teal and amber tones with checkered accents"></div>

    <div class="shop-name"><span class="shop-name__mark"></span><span>Ridgeway Auto &amp; Lube</span></div>

    <h1 class="headline">Burleson’s<br>Premier Auto&nbsp;&nbsp;&amp;<br>Diesel Repair Shop!</h1>

    <div class="phone-band"></div>
    <div class="neon-rule neon-rule--top"></div>
    <div class="neon-rule neon-rule--bottom"></div>
    <p class="phone">817-390-7148</p>

    <svg class="cert-badge" width="116" height="116" viewBox="0 0 116 116" aria-hidden="true">
      <circle cx="58" cy="58" r="55" fill="var(--badge-blue)"/>
    </svg>

    <p class="tagline">Best auto repair shop in town!</p>

    <svg class="directions" width="530" height="180" viewBox="0 0 530 180" aria-hidden="true">
      <path d="M10 42 H436 V2 L524 90 L436 178 V136 H10 Z" fill="var(--white)"/>
      <path d="M18 50 H444 V20 L512 90 L444 160 V126 H18 Z" fill="var(--royal-blue)"/>
    </svg>
    <p class="directions__distance">1.2 miles ahead</p>
    <p class="directions__address">2085 W Malbury St</p>

    <div class="neon-frame"></div>
  </section>
</body>
</html>
```